Norrell Advisory WA Business Card

Create an interesting, eye catching and colourful two sided business card. We are a business consulting operation assisting SME's improve all areas of their business. We provide consulting services to assist SME's to create a culture of continuous improvement, making a positive difference in the business. Our tag line is Small changes, big rewards. We want to create a well recognised, innovative brand that can be continued throughout our website, social media and email correspondence.

Target Market(s)

Small to Medium Enterprise Business Owners

Industry/Entity Type

Business Consultant

Contact Information for Business Card

Name of Business: Norrell Advisory - Steady Steps Lasting Gains
Derek Holloway Ph 0407385510 Megan Holloway Ph 0407913847
Email norrelladvisorywa@mailbox-example.com
Web address TBA
FaceBook page TBA

BACKSIDE OF CARD

Providing assistance with:

• Organisation & Efficiency
• Revenue generation & Marketing
• Financial Management
• Production quality & delivery
• Systems & Process documentation
• Exit Strategy

Font styles to use
Other font styles liked:
• Calibri

Colors

Designer to choose colors to be used in the design.

Requirements
Must have
• Calibri font

```html
<!DOCTYPE html>
<html lang="en">
<head>
<meta charset="utf-8">
<title>Norrell Advisory WA Business Card</title>
<link rel="stylesheet" href="https://fonts.googleapis.com/css2?family=Carlito:wght@400;700&display=swap">
<style>
  :root {
    --page: #e4e4e4;
    --card: #ffffff;
    --band: #1b1c1e;
    --brand-blue: #1a78b8;
    --ink: #2e2e2e;
    --muted: #555a5e;
    --white: #ffffff;
    --divider: #d9d9d9;
    --pattern-red: #7e2a24;
    --pattern-olive: #6a7a2c;
    --pattern-teal: #2c5d74;
    --pattern-gold: #8a7228;
  }
  * { box-sizing: border-box; margin: 0; padding: 0; }
  html, body {
    width: 1125px; height: 1200px; overflow: hidden;
    background: var(--page);
    font-family: "Carlito", "Calibri", sans-serif;
  }
  .canvas { position: relative; width: 1125px; height: 1200px; }
  .card {
    position: absolute; left: 171px; width: 826px; height: 472px;
    border-radius: 22px; overflow: hidden; background: var(--card);
  }
  .card--front { top: 106px; }
  .card--back { top: 640px; }

  .pattern {
    position: absolute; left: 0; width: 100%;
    background: linear-gradient(120deg, var(--pattern-olive) 0%, var(--pattern-teal) 25%, var(--pattern-red) 50%, var(--pattern-gold) 72%, var(--pattern-teal) 100%);
  }
  .pattern--top { top: 0; height: 147px; }
  .pattern--bottom { top: 323px; height: 149px; }

  .contact-band {
    position: absolute; left: 0; top: 147px; width: 100%; height: 176px;
    background: var(--band);
  }
  .holder {
    position: absolute; right: 459px; top: 50px; text-align: right;
  }
  .holder__name {
    font-weight: 700; font-size: 40px; line-height: 1; color: var(--brand-blue);
  }
  .holder__phone {
    margin-top: 4px; font-weight: 700; font-size: 23px; color: var(--white);
  }
  .band-divider {
    position: absolute; left: 402px; top: 40px; width: 2px; height: 96px;
    background: linear-gradient(180deg, transparent, var(--divider) 30%, var(--divider) 70%, transparent);
  }
  .contact-list {
    position: absolute; left: 444px; top: 47px; list-style: none;
  }
  .contact-list li {
    display: flex; align-items: center; height: 25px;
    font-size: 18.5px; color: var(--white);
  }
  .contact-list svg { width: 18px; height: 18px; margin-right: 11px; flex: none; }

  .brand {
    position: absolute; left: 40px; top: 120px; width: 310px; text-align: center;
  }
  .brand__mark {
    display: block; width: 96px; height: 96px; margin: 0 auto 26px;
    background: var(--brand-blue);
  }
  .brand__name {
    font-weight: 700; font-size: 30px; line-height: 1; color: var(--ink);
    letter-spacing: 0.3px;
  }
  .brand__tagline {
    margin-top: 4px; font-size: 17px; letter-spacing: 1.8px; color: var(--muted);
  }
  .services { position: absolute; left: 427px; top: 122px; }
  .services__title {
    font-weight: 700; font-size: 29px; color: var(--brand-blue); line-height: 1;
  }
  .services__list { list-style: none; margin-top: 16px; }
  .services__list li {
    display: flex; align-items: center; height: 26.2px;
    font-size: 19px; color: var(--muted);
  }
  .services__list li::before {
    content: ""; width: 10px; height: 10px; border-radius: 50%;
    background: var(--brand-blue); margin: 0 9px 0 3px; flex: none;
  }
</style>
</head>
<body>
<main class="canvas">
  <section class="card card--front">
    <div class="pattern pattern--top" role="img" aria-label="Colourful interlocking puzzle-piece pattern in red, olive, teal and gold"></div>
    <div class="contact-band">
      <div class="holder">
        <p class="holder__name">Megan Holloway</p>
        <p class="holder__phone">0407913847</p>
      </div>
      <div class="band-divider"></div>
      <ul class="contact-list">
        <li>
          <svg viewBox="0 0 18 18" aria-hidden="true"><rect x="1" y="4" width="16" height="11" fill="#1a78b8"/><path d="M1 4l8 6 8-6" fill="none" stroke="#1b1c1e" stroke-width="1.4"/></svg>
          norrelladvisorywa@mailbox-example.com
        </li>
        <li>
          <svg viewBox="0 0 18 18" aria-hidden="true"><circle cx="9" cy="9" r="7.5" fill="#1a78b8"/><path d="M1.5 9h15M9 1.5c-3 3.5-3 11.5 0 15M9 1.5c3 3.5 3 11.5 0 15" fill="none" stroke="#1b1c1e" stroke-width="1.1"/></svg>
          www.norrelladvisorywa.com
        </li>
        <li>
          <svg viewBox="0 0 18 18" aria-hidden="true"><rect x="2" y="2" width="14" height="14" fill="#1a78b8"/></svg>
          norrelladvisorywa
        </li>
      </ul>
    </div>
    <div class="pattern pattern--bottom" role="img" aria-label="Colourful interlocking puzzle-piece pattern in red, olive, teal and gold"></div>
  </section>

  <section class="card card--back">
    <div class="brand">
      <span class="brand__mark"></span>
      <p class="brand__name">NORRELL ADVISORY</p>
      <p class="brand__tagline">STEADY STEPS LASTING GAINS</p>
    </div>
    <div class="services">
      <h2 class="services__title">Providing assistance with</h2>
      <ul class="services__list">
        <li>Organisation &amp; Efficiency</li>
        <li>Revenue generation &amp; Marketing</li>
        <li>Financial Management</li>
        <li>Production quality &amp; delivery</li>
        <li>Systems &amp; Process documentation</li>
        <li>Exit Strategy</li>
      </ul>
    </div>
  </section>
</main>
</body>
</html>
```